Business Card Design

We are looking for a business card designed for our landscaping company. We do landscaping installation & Maintenance Services. We would like to see designs that have basic landscaping in background. We also think it is important to have both of our names and phone numbers on the card. We need something that stands out a little whether it is shape of the card or thickness or design.

Business

Bramblewood Yardworks, bramblewoodyard@mailvista.net, Owen Platt 555-273-9104, Daniel Korbin 555-618-3927

```html
<!DOCTYPE html>
<html lang="en">
<head>
<meta charset="utf-8">
<title>Bramblewood Yardworks – Business Card</title>
<link href="https://fonts.googleapis.com/css2?family=Playfair+Display:wght@500;600&family=Open+Sans:wght@400&display=swap" rel="stylesheet">
<style>
  :root {
    --backdrop: #e9e6e1;
    --card-black: #0b0b0b;
    --gold-light: #f1df9c;
    --gold-mid: #d9bf6a;
    --gold-deep: #b8973f;
    --title-silver: #eeeeee;
    --email-grey: #d4d4d4;
    --ink: #1a1608;
  }
  html, body {
    margin: 0;
    width: 1200px;
    height: 902px;
    overflow: hidden;
    background: var(--backdrop);
  }
  .stage {
    width: 1200px;
    height: 902px;
    display: flex;
    align-items: center;
    justify-content: center;
  }
  .business-card {
    position: relative;
    width: 1000px;
    height: 571px;
    overflow: hidden;
    border-radius: 4px;
    box-shadow: 0 14px 40px rgba(0,0,0,.25);
    background:
      repeating-linear-gradient(90deg, rgba(255,255,255,.10) 0 1px, rgba(0,0,0,0) 1px 4px, rgba(120,90,20,.06) 4px 5px),
      linear-gradient(120deg, var(--gold-mid) 0%, var(--gold-light) 45%, var(--gold-mid) 75%, var(--gold-deep) 100%);
  }
  .card-art {
    position: absolute;
    inset: 0;
  }
  .company-name {
    position: absolute;
    left: 70px;
    top: 150px;
    margin: 0;
    font-family: "Playfair Display", serif;
    font-weight: 600;
    font-size: 58px;
    letter-spacing: .5px;
    color: var(--title-silver);
    text-shadow: 0 2px 3px rgba(0,0,0,.6);
  }
  .company-email {
    position: absolute;
    left: 74px;
    top: 232px;
    margin: 0;
    font-family: "Open Sans", sans-serif;
    font-size: 25px;
    color: var(--email-grey);
  }
  .contact {
    position: absolute;
    font-family: "Open Sans", sans-serif;
    color: var(--ink);
  }
  .contact-name {
    display: block;
    font-family: "Playfair Display", serif;
    font-weight: 500;
    font-size: 36px;
    line-height: 1.1;
  }
  .contact-phone {
    display: flex;
    align-items: center;
    gap: 12px;
    font-size: 26px;
    margin-top: 4px;
    padding-left: 56px;
  }
  .phone-icon {
    width: 20px;
    height: 20px;
  }
  .contact--first { left: 610px; top: 300px; }
  .contact--second { left: 650px; top: 420px; }
</style>
</head>
<body>
<main class="stage">
  <article class="business-card">
    <svg class="card-art" viewBox="0 0 1000 571" aria-hidden="true">
      <defs>
        <linearGradient id="ribbonGold" x1="0" y1="0" x2="1" y2="0">
          <stop offset="0" stop-color="#a88532"/>
          <stop offset=".3" stop-color="#f7e59e"/>
          <stop offset=".55" stop-color="#c9a448"/>
          <stop offset=".8" stop-color="#fbeaa8"/>
          <stop offset="1" stop-color="#b18e3a"/>
        </linearGradient>
      </defs>
      <path class="ribbon-shadow" d="M0,472 C300,472 420,440 560,330 C690,228 800,168 1000,160" fill="none" stroke="rgba(90,65,10,.35)" stroke-width="30"/>
      <path class="ribbon" d="M0,462 C300,462 420,430 560,320 C690,218 800,158 1000,150" fill="none" stroke="url(#ribbonGold)" stroke-width="26"/>
      <path class="black-field" d="M0,0 H1000 V140 C800,148 690,206 560,308 C420,418 300,450 0,450 Z" fill="var(--card-black)"/>
    </svg>

    <h1 class="company-name">Bramblewood Yardworks</h1>
    <p class="company-email">bramblewoodyard@mailvista.net</p>

    <div class="contact contact--first">
      <span class="contact-name">Daniel Korbin</span>
      <span class="contact-phone">555-618-3927
        <svg class="phone-icon" viewBox="0 0 20 20" aria-hidden="true"><rect width="20" height="20" fill="#111"/><path d="M6,4 l3,0 1,4 -2,1 c1,2 2,3 4,4 l1,-2 4,1 0,3 c-6,1 -12,-5 -11,-11z" fill="#f1df9c"/></svg>
      </span>
    </div>

    <div class="contact contact--second">
      <span class="contact-name">Owen Platt</span>
      <span class="contact-phone">555-273-9104
        <svg class="phone-icon" viewBox="0 0 20 20" aria-hidden="true"><rect width="20" height="20" fill="#111"/><path d="M6,4 l3,0 1,4 -2,1 c1,2 2,3 4,4 l1,-2 4,1 0,3 c-6,1 -12,-5 -11,-11z" fill="#f1df9c"/></svg>
      </span>
    </div>
  </article>
</main>
</body>
</html>
```